Ward Compass Business Card Design*

We need a business card design for our company Ward Compass. Our company is specialized in providing online consulting services regarding medical institutions, hospitals and doctors. We work with patients worldwide looking to choose between healthcare providers. We have a website you may use as a reference, where we list doctors and clinics worldwide. So we target Medical providers as well as patients worldwide.
Target Market(s)
Medical Providers and patients around the world
Industry/Entity Type
Medical
Contact Information for Business Card
Salwa Kettani
CEO
+90 612 348 2175
info@wardcompass.example
www.wardcompass.example
14 Annakhil 7 H.R.B. Rabat, Morocco
Requirements
Must have
- Company logo/name on one full side, personal info and smaller logo and company name on the other side.
Nice to have
- Smart and elegant design

```html
<!DOCTYPE html>
<html lang="en">
<head>
<meta charset="utf-8">
<title>Ward Compass Business Card</title>
<link rel="stylesheet" href="https://fonts.googleapis.com/css2?family=Montserrat:wght@400;600;700&display=swap">
<style>
  :root {
    --navy: #1c3461;
    --grey: #6f7072;
    --light-grey: #8a8b8d;
    --card: #f4f4f4;
    --backdrop: #2a2a2a;
  }
  * { margin: 0; padding: 0; box-sizing: border-box; }
  html, body { width: 1200px; height: 997px; overflow: hidden; }
  body {
    background: var(--backdrop);
    font-family: "Montserrat", Arial, sans-serif;
    display: flex;
    flex-direction: column;
    align-items: center;
    justify-content: center;
    gap: 56px;
  }
  .card {
    position: relative;
    width: 700px;
    height: 400px;
    background: linear-gradient(160deg, #ffffff 0%, var(--card) 60%, #e9e9e9 100%);
    border-radius: 18px;
    overflow: hidden;
  }
  .card__edge {
    position: absolute;
    left: 0;
    bottom: 0;
    width: 700px;
    height: 60px;
  }
  .edge__band { fill: var(--navy); }
  .edge__tab { fill: var(--light-grey); }

  /* front */
  .card--front .brand {
    position: absolute;
    left: 0; right: 0;
    top: 130px;
    display: flex;
    align-items: center;
    justify-content: center;
    gap: 18px;
  }
  .brand__dot {
    width: 34px; height: 34px;
    border-radius: 50%;
    background: var(--navy);
  }
  .brand__name {
    font-weight: 600;
    color: var(--navy);
    letter-spacing: 0.06em;
    text-transform: uppercase;
  }
  .card--front .brand__name { font-size: 46px; }
  .address {
    position: absolute;
    left: 0; right: 0;
    top: 210px;
    text-align: center;
    font-size: 17px;
    font-weight: 600;
    letter-spacing: 0.08em;
    color: var(--grey);
    text-transform: uppercase;
  }
  .address__city { color: var(--navy); }

  /* back */
  .card--back .brand {
    position: absolute;
    left: 150px;
    top: 96px;
    display: flex;
    align-items: center;
    gap: 14px;
  }
  .card--back .brand__dot { width: 26px; height: 26px; }
  .card--back .brand__name { font-size: 30px; }
  .person {
    position: absolute;
    left: 170px;
    top: 232px;
  }
  .person__name {
    font-size: 20px;
    font-weight: 700;
    color: var(--navy);
    text-transform: uppercase;
    letter-spacing: 0.02em;
  }
  .person__role {
    font-size: 14px;
    font-weight: 700;
    color: var(--grey);
  }
  .divider {
    position: absolute;
    left: 388px;
    top: 186px;
    width: 2px;
    height: 90px;
    background: linear-gradient(to bottom, transparent, var(--navy), transparent);
  }
  .contacts {
    position: absolute;
    left: 412px;
    top: 192px;
    list-style: none;
    display: flex;
    flex-direction: column;
    gap: 8px;
  }
  .contacts__item {
    display: flex;
    align-items: center;
    gap: 12px;
    font-size: 14px;
    color: var(--grey);
  }
  .contacts__icon { width: 14px; height: 14px; fill: var(--navy); flex: none; }
</style>
</head>
<body>
  <section class="card card--front" aria-label="Card front">
    <div class="brand">
      <span class="brand__dot"></span>
      <span class="brand__name">Ward Compass</span>
    </div>
    <p class="address">14 Annakhil 7 H.R.B. <span class="address__city">Rabat, Morocco</span></p>
    <svg class="card__edge" viewBox="0 0 700 60" aria-hidden="true">
      <polygon class="edge__band" points="0,50 580,14 700,14 700,60 0,60"/>
      <polygon class="edge__tab" points="580,14 602,0 700,0 700,14"/>
    </svg>
  </section>

  <section class="card card--back" aria-label="Card back">
    <div class="brand">
      <span class="brand__dot"></span>
      <span class="brand__name">Ward Compass</span>
    </div>
    <div class="person">
      <p class="person__name">Salwa Kettani</p>
      <p class="person__role">CEO</p>
    </div>
    <span class="divider"></span>
    <ul class="contacts">
      <li class="contacts__item">
        <svg class="contacts__icon" viewBox="0 0 16 16" aria-hidden="true"><path d="M3 1h3l1.5 4-2 1.3a9 9 0 0 0 4.2 4.2L11 8.5l4 1.5v3a2 2 0 0 1-2 2A13 13 0 0 1 1 3a2 2 0 0 1 2-2z"/></svg>
        +90 612 348 2175
      </li>
      <li class="contacts__item">
        <svg class="contacts__icon" viewBox="0 0 16 16" aria-hidden="true"><path d="M1 3h14v10H1z M2 4l6 5 6-5" fill="none" stroke="var(--navy)" stroke-width="1.6"/></svg>
        info@wardcompass.example
      </li>
      <li class="contacts__item">
        <svg class="contacts__icon" viewBox="0 0 16 16" aria-hidden="true"><circle cx="8" cy="8" r="6.5" fill="none" stroke="var(--navy)" stroke-width="1.5"/><path d="M1.5 8h13M8 1.5c-3 3.5-3 9.5 0 13M8 1.5c3 3.5 3 9.5 0 13" fill="none" stroke="var(--navy)" stroke-width="1.2"/></svg>
        www.wardcompass.example
      </li>
    </ul>
    <svg class="card__edge" viewBox="0 0 700 60" aria-hidden="true">
      <polygon class="edge__band" points="0,50 580,14 700,14 700,60 0,60"/>
      <polygon class="edge__tab" points="580,14 602,0 700,0 700,14"/>
    </svg>
  </section>
</body>
</html>
```